U.S. Popcorn company needs business cards

We are a popcorn company that manufactures popcorn and sells it to grocery stores worldwide. Our theme is "Americana" and our logo is U.S. route 66 which is the most famous highway in the U.S.

We would like the design to be simple and to use both sides. On the back side we would like to see just the logo and website. The front would be normal details

Target Market(s)

Wholesalers, grocers and distributors

Industry/Entity Type

Manufacture

Contact Information for Business Card

Business name: Prairie Lantern Popcorn
Phone: +1 555 308 4726
Email: Dale@prairielanternpopcorn.com
website: www.prairielanternpopcorn.com
Tag Line: "POPular for a reason"
Name: Dale Whitcombe
Title: Founder/President

Requirements
Must have
• Either this design should be fun or clean and simple. I will let you show me your thougths.
Nice to have
• Anything that ties in the real Hwy Route 66.
• Colors might need to be red, white and blue incorporated.
Should not have
• Not be too busy.

```html
<!DOCTYPE html>
<html lang="en">
<head>
<meta charset="utf-8">
<title>Prairie Lantern Popcorn – Business Cards</title>
<link rel="stylesheet" href="https://fonts.googleapis.com/css2?family=Source+Sans+3:ital,wght@0,400;0,600;0,700;1,600&display=swap">
<style>
  :root {
    --navy: #062566;
    --navy-light: #14387e;
    --red: #e0262f;
    --white: #ffffff;
    --road: #111111;
    --backdrop: #e9e9e9;
  }
  * { margin: 0; padding: 0; box-sizing: border-box; }
  html, body {
    width: 1200px; height: 987px; overflow: hidden;
    background: var(--backdrop);
    font-family: "Source Sans 3", "Myriad Pro", Arial, sans-serif;
  }
  .card {
    position: absolute; left: 293px; width: 615px; height: 352px;
    box-shadow: 0 2px 4px rgba(0,0,0,.25);
    overflow: hidden;
  }
  .card--front { top: 130px; display: flex; }
  .card--back  { top: 505px; background: var(--navy); }

  .details {
    width: 316px; background: var(--navy); color: var(--white);
    position: relative;
  }
  .details__name {
    position: absolute; right: 32px; top: 110px;
    color: var(--red); font-size: 22px; font-weight: 600;
  }
  .details__title {
    position: absolute; right: 32px; top: 140px;
    font-size: 17px;
  }
  .contact { position: absolute; right: 8px; top: 175px; list-style: none; }
  .contact__item {
    display: flex; align-items: center; justify-content: flex-end;
    font-size: 16px; height: 23.5px; gap: 10px;
  }
  .contact__icon { width: 14px; height: 14px; fill: var(--red); }

  .road-stripe {
    width: 8px; background: var(--road);
    display: flex; justify-content: center;
  }
  .road-stripe::after {
    content: ""; width: 2px; height: 100%;
    background: repeating-linear-gradient(to bottom, var(--white) 0 4px, transparent 4px 8px);
  }

  .brand-panel {
    flex: 1; background: var(--white);
    display: flex; align-items: center; justify-content: center;
  }
  .brand-name {
    font-weight: 700; font-size: 30px; line-height: 1.05;
    text-align: center; text-transform: uppercase;
  }
  .brand-panel .brand-name { color: var(--navy); }

  .sunburst {
    position: absolute; inset: 0;
    background: radial-gradient(circle at 50% 45%, var(--navy-light) 0%, var(--navy) 70%);
  }
  .back-content {
    position: absolute; inset: 0;
    display: flex; flex-direction: column; align-items: center;
  }
  .back-content .brand-name {
    color: var(--white); font-size: 40px; margin-top: 92px;
  }
  .tagline {
    position: absolute; top: 296px; width: 100%; text-align: center;
    color: var(--white); font-size: 18px; font-style: italic; font-weight: 600;
  }
  .tagline strong { font-style: normal; font-weight: 700; }
</style>
</head>
<body>

<section class="card card--front">
  <div class="details">
    <p class="details__name">Dale Whitcombe</p>
    <p class="details__title">Founder/President</p>
    <ul class="contact">
      <li class="contact__item">+1 555 308 4726
        <svg class="contact__icon" viewBox="0 0 16 16" aria-hidden="true"><path d="M3 1l3 3-1.5 2c1 2 3 4 5 5L11.5 9.5l3 3-2 2.5C6 14 2 10 1 3z"/></svg>
      </li>
      <li class="contact__item">Dale@prairielanternpopcorn.com
        <svg class="contact__icon" viewBox="0 0 16 16" aria-hidden="true"><path d="M1 3h14v10H1z M1 3l7 6 7-6" stroke="#062566" stroke-width="1.2"/></svg>
      </li>
      <li class="contact__item">www.prairielanternpopcorn.com
        <svg class="contact__icon" viewBox="0 0 16 16" aria-hidden="true"><circle cx="8" cy="8" r="7"/><path d="M1 8h14M8 1c-3 4-3 10 0 14M8 1c3 4 3 10 0 14" stroke="#062566" stroke-width="1.2" fill="none"/></svg>
      </li>
    </ul>
  </div>
  <div class="road-stripe"></div>
  <div class="brand-panel">
    <p class="brand-name">Prairie Lantern<br>Popcorn</p>
  </div>
</section>

<section class="card card--back">
  <div class="sunburst" role="img" aria-label="Navy sunburst rays radiating from the centre"></div>
  <div class="back-content">
    <p class="brand-name">Prairie Lantern<br>Popcorn</p>
    <p class="tagline"><strong>POP</strong>ular for a reason</p>
  </div>
</section>

</body>
</html>
```